Kinesiology undergraduate program needs an infographic

We would like an infographic to creatively and succinctly inform students, faculty, staff, and others about our undergraduate values and competencies (perhaps also integrating our mission and vision). We would like to see a design that incorporates the definition of Kinesiology (the study of human movement) and the colors of our Westbrook State University at Harlan.

```html
<!DOCTYPE html>
<html lang="en">
<head>
<meta charset="utf-8">
<title>Kinesiology Undergraduate Program – Mission, Vision and Values</title>
<link rel="stylesheet" href="https://fonts.googleapis.com/css2?family=Amatic+SC:wght@700&family=Montserrat:wght@400;800&display=swap">
<style>
  :root {
    --paper: #ffffff;
    --rule: #d4d4d6;
    --rule-strong: #a9a9ac;
    --margin-red: #f2a3a3;
    --brand-red: #e1101e;
    --navy: #2c2a5c;
    --body-text: #3a3a3a;
    --ink: #111111;
    --circle-grey: #e6e6e8;
  }
  * { margin: 0; padding: 0; box-sizing: border-box; }
  html, body { width: 1200px; height: 848px; overflow: hidden; background: var(--paper); }
  .infographic {
    position: relative;
    width: 1200px;
    height: 848px;
    overflow: hidden;
    background:
      linear-gradient(to right, transparent 147px, var(--margin-red) 147px, var(--margin-red) 149px, transparent 149px, transparent 156px, var(--margin-red) 156px, var(--margin-red) 158px, transparent 158px),
      repeating-linear-gradient(to bottom, transparent 0, transparent 47px, var(--rule) 47px, var(--rule) 49px, transparent 49px, transparent 51.2px),
      var(--paper);
    font-family: "Montserrat", sans-serif;
    color: var(--body-text);
  }
  .rule-strong { position: absolute; left: 0; width: 1200px; height: 2px; background: var(--rule-strong); }
  .section-title {
    position: absolute;
    font-family: "Amatic SC", cursive;
    font-weight: 700;
    color: var(--brand-red);
    font-size: 62px;
    line-height: 1;
    text-align: center;
    letter-spacing: 1px;
  }
  .statement {
    position: absolute;
    text-align: center;
    font-size: 15.5px;
    line-height: 20.6px;
  }
  .competency { position: absolute; font-size: 15.5px; line-height: 20.5px; }
  .competency h3 {
    font-weight: 800;
    color: var(--navy);
    font-size: 15.5px;
    line-height: 20px;
    text-transform: uppercase;
  }
  .competency ul { list-style: none; }
  .students-illustration {
    position: absolute;
    left: 370px;
    top: 250px;
    width: 460px;
    height: 560px;
    border-radius: 50% 50% 12px 12px;
    background:
      radial-gradient(circle at 50% 42%, var(--circle-grey) 0, var(--circle-grey) 48%, transparent 49%),
      radial-gradient(ellipse at 50% 60%, rgba(192,22,34,0.35) 0, rgba(192,22,34,0.12) 30%, transparent 55%);
  }
  .overlay { position: absolute; left: 0; top: 0; }
</style>
</head>
<body>
<main class="infographic">
  <div class="rule-strong" style="top:202px"></div>
  <div class="rule-strong" style="top:304px"></div>

  <div class="students-illustration" role="img" aria-label="Illustration of two smiling kinesiology students in red shirts with backpacks, waving, in front of a light grey circle"></div>

  <h2 class="section-title" style="left:450px; top:56px; width:300px;">Our Mission</h2>
  <p class="statement" style="left:400px; top:108px; width:400px;">To empower undergraduate students<br>to pursue excellence through<br>scientific discovery, clinical practice,<br>and health promotion</p>

  <h2 class="section-title" style="left:92px; top:190px; width:280px;">Our Values</h2>
  <p class="statement" style="left:92px; top:244px; width:280px;">Student Success, Science,<br>and Service<br>Our Graduates Will Be<br>Competent In...</p>

  <h2 class="section-title" style="left:838px; top:190px; width:280px;">Our Vision</h2>
  <p class="statement" style="left:838px; top:244px; width:280px;">WSUH Kinesiology graduates<br>are leaders who excel in<br>careers that enhance the<br>quality of life of individuals<br>and communities</p>

  <section class="competency" style="left:123px; top:492px;">
    <h3>Intrapersonal Growth</h3>
    <ul><li>Cultural Humility/Sensitivity</li><li>Integrity</li><li>Self-Directed</li><li>Dependability</li><li>Mission Oriented</li></ul>
  </section>

  <section class="competency" style="left:123px; top:652px;">
    <h3>The Science of<br>Kinesiology</h3>
    <ul><li>Foundational Concepts of</li><li>Kinesiology</li><li>Clinical Application</li><li>Scientific Communication</li></ul>
  </section>

  <section class="competency" style="left:860px; top:492px;">
    <h3>Thinking and Reasoning</h3>
    <ul><li>Critical Thinking</li><li>Quantitative Reasoning</li><li>Scientific Inquiry</li><li>Concept Integration</li></ul>
  </section>

  <section class="competency" style="left:860px; top:652px;">
    <h3>Relationships and<br>Communication</h3>
    <ul><li>Cultural Competence</li><li>Professionalism</li><li>Leadership and Teamwork</li><li>Service</li><li>Orientation/Citizenship</li></ul>
  </section>

  <svg class="overlay" width="1200" height="848" viewBox="0 0 1200 848" aria-hidden="true">
    <polygon points="217,340 233,340 225,355" fill="var(--navy)"/>
    <g fill="none" stroke="var(--ink)" stroke-width="1.5">
      <polyline points="355,397 97,397 97,496"/>
      <polyline points="415,610 385,610 385,665 310,665"/>
      <polyline points="785,385 805,385 805,496 828,496"/>
      <polyline points="748,573 800,573 800,665 828,665"/>
    </g>
    <g fill="var(--ink)">
      <circle cx="355" cy="397" r="5"/><circle cx="97" cy="496" r="5"/>
      <circle cx="415" cy="610" r="5"/><circle cx="310" cy="665" r="5"/>
      <circle cx="785" cy="385" r="5"/><circle cx="828" cy="496" r="5"/>
      <circle cx="748" cy="573" r="5"/><circle cx="828" cy="665" r="5"/>
    </g>
    <!-- pencil icon -->
    <g fill="none" stroke="var(--navy)" stroke-width="3" stroke-linejoin="round">
      <polygon points="122,428 134,416 167,449 170,470 148,466 115,433"/>
      <line x1="117" y1="431" x2="130" y2="418"/>
      <line x1="150" y1="464" x2="164" y2="450"/>
    </g>
    <!-- atom icon -->
    <g fill="none" stroke="var(--navy)" stroke-width="3">
      <ellipse cx="76" cy="662" rx="36" ry="13"/>
      <ellipse cx="76" cy="662" rx="36" ry="13" transform="rotate(60 76 662)"/>
      <ellipse cx="76" cy="662" rx="36" ry="13" transform="rotate(-60 76 662)"/>
      <circle cx="76" cy="662" r="5" fill="var(--navy)"/>
    </g>
    <!-- light bulb icon -->
    <g fill="none" stroke="var(--navy)" stroke-width="3" stroke-linecap="round">
      <path d="M1117,494 C1101,484 1103,452 1128,452 C1153,452 1155,484 1139,494 L1139,503 L1117,503 Z"/>
      <line x1="1119" y1="509" x2="1137" y2="509"/>
      <line x1="1121" y1="515" x2="1135" y2="515"/>
      <line x1="1128" y1="440" x2="1128" y2="432"/>
      <line x1="1102" y1="448" x2="1096" y2="442"/>
      <line x1="1154" y1="448" x2="1160" y2="442"/>
      <line x1="1093" y1="470" x2="1085" y2="470"/>
      <line x1="1163" y1="470" x2="1171" y2="470"/>
      <line x1="1097" y1="490" x2="1091" y2="494"/>
      <line x1="1159" y1="490" x2="1165" y2="494"/>
    </g>
    <!-- communication emblem icon -->
    <g fill="none" stroke="var(--navy)" stroke-width="3">
      <circle cx="1096" cy="660" r="37"/>
      <circle cx="1096" cy="660" r="27"/>
      <polygon points="1096,642 1101,654 1114,655 1104,663 1107,676 1096,669 1085,676 1088,663 1078,655 1091,654"/>
      <circle cx="1096" cy="660" r="5" fill="var(--navy)"/>
    </g>
  </svg>
</main>
</body>
</html>
```